Dalvick's Business Card

I need some designs for a new business card including the new logo attached. An old example of our business card is also attached to show all the data that should be included on the new design.
**I added some more examples someone had mocked up**

Contact Information for Business Card

Should include all info on other examples uploaded.

```html
<!DOCTYPE html>
<html lang="en">
<head>
<meta charset="utf-8">
<title>Dalvick's Business Card</title>
<link rel="stylesheet" href="https://fonts.googleapis.com/css2?family=Fira+Sans:wght@600;700&family=Fira+Sans+Condensed:wght@400;600&display=swap">
<style>
  :root {
    --bg: #e4e4e4;
    --blue: #0b6db5;
    --red: #e42128;
    --black: #222222;
    --white: #ffffff;
    --paper: #f4f4f4;
  }
  html, body { margin: 0; padding: 0; overflow: hidden; }
  body { width: 1200px; height: 960px; background: var(--bg); position: relative; font-family: "Fira Sans", sans-serif; }
  .card { position: absolute; left: 294px; width: 614px; height: 350px; overflow: hidden; }
  .card svg.bands { position: absolute; inset: 0; }
  .card-front { top: 106px; background: var(--black); }
  .card-back { top: 511px; background: var(--paper); }
  .line { position: absolute; left: 0; width: 100%; text-align: center; color: var(--white); font-weight: 600; margin: 0; }
  .claims { top: 22px; font-size: 19px; line-height: 27px; letter-spacing: .2px; }
  .service { top: 286px; font-size: 18px; line-height: 24px; }
  .service span { display: block; font-size: 17px; }
  .brand { position: absolute; display: flex; align-items: center; gap: 14px; color: var(--blue); font-weight: 700; }
  .brand .dot { border-radius: 50%; background: var(--red); }
  .front-brand { left: 92px; top: 138px; font-size: 58px; }
  .front-brand .dot { width: 48px; height: 48px; }
  .back-brand { left: 48px; top: 48px; font-size: 40px; }
  .back-brand .dot { width: 34px; height: 34px; }
  .contact { position: absolute; left: 44px; top: 206px; font-family: "Fira Sans Condensed", sans-serif; color: var(--white); }
  .name { margin: 0; color: var(--blue); font-weight: 600; font-size: 22px; }
  .role { margin: 2px 0 20px; color: var(--red); font-size: 16px; }
  .detail { display: flex; align-items: center; gap: 7px; font-size: 16px; margin: 0 0 5px; }
  .area { position: absolute; right: 26px; top: 303px; font-family: "Fira Sans Condensed", sans-serif; color: var(--white); font-size: 17px; margin: 0; }
  .faint-mark { position: absolute; left: 400px; top: 20px; width: 170px; height: 170px; border-radius: 50%; background: rgba(11,109,181,.07); }
</style>
</head>
<body>
  <section class="card card-front">
    <svg class="bands" viewBox="0 0 614 350" width="614" height="350" aria-hidden="true">
      <path d="M0,0 H614 V50 Q307,110 0,50 Z" fill="var(--blue)"/>
      <path d="M0,50 Q307,110 614,50" fill="none" stroke="var(--white)" stroke-width="4"/>
      <path d="M0,296 Q307,230 614,296 V350 H0 Z" fill="var(--red)"/>
      <path d="M0,296 Q307,230 614,296" fill="none" stroke="var(--white)" stroke-width="4"/>
    </svg>
    <p class="line claims">FAMILY OWNED &amp; OPERATED<br>LICENSED &amp; INSURED</p>
    <div class="brand front-brand"><span class="dot"></span>Dalvick's</div>
    <p class="line service">Serves Millbrook, IA &amp; Surrounding Areas<span>Call Today For All Your Hvac, Refrigeration &amp; Plumbing Needs</span></p>
  </section>

  <section class="card card-back">
    <div class="faint-mark"></div>
    <svg class="bands" viewBox="0 0 614 350" width="614" height="350" aria-hidden="true">
      <path d="M0,165 C150,130 300,190 450,215 C530,228 590,222 614,195 L614,215 C580,232 520,238 450,228 C300,205 150,150 0,200 Z" fill="var(--red)"/>
      <path d="M0,200 C150,150 300,205 450,228 C520,238 580,232 614,215 V350 H0 Z" fill="var(--black)"/>
      <path d="M0,200 C150,150 300,205 450,228 C520,238 580,232 614,215" fill="none" stroke="var(--white)" stroke-width="3"/>
      <path d="M230,350 C280,290 380,268 480,252 C560,240 600,212 614,178 V350 Z" fill="var(--blue)" stroke="var(--white)" stroke-width="5"/>
    </svg>
    <div class="brand back-brand"><span class="dot"></span>Dalvick's</div>
    <div class="contact">
      <p class="name">MASON DALVICK</p>
      <p class="role">CO-OWNER</p>
      <p class="detail">
        <svg width="15" height="15" viewBox="0 0 24 24" aria-hidden="true"><path d="M6.6 10.8a15 15 0 0 0 6.6 6.6l2.2-2.2a1 1 0 0 1 1-.25 11.4 11.4 0 0 0 3.6.57 1 1 0 0 1 1 1V20a1 1 0 0 1-1 1A17 17 0 0 1 3 4a1 1 0 0 1 1-1h3.5a1 1 0 0 1 1 1c0 1.25.2 2.45.57 3.6a1 1 0 0 1-.25 1z" fill="var(--red)"/></svg>
        555.014.2870
      </p>
      <p class="detail">
        <svg width="16" height="12" viewBox="0 0 24 18" aria-hidden="true"><rect x="1.5" y="1.5" width="21" height="15" fill="none" stroke="var(--red)" stroke-width="2.5"/><path d="M2 2l10 8 10-8" fill="none" stroke="var(--red)" stroke-width="2.5"/></svg>
        hvacdalvick@example.com
      </p>
    </div>
    <p class="area">Serves Millbrook, IA &amp; Surrounding Areas</p>
  </section>
</body>
</html>
```